Marwick Partners Exit Plan business consultant web site

This website is for a consulting business that helps other businesses with exit plans. Essentially, assists them with the sale of their business. This website should be very professional, almost with a wall street look. I would like a very attractive image on the homepage. Perhaps something that denotes success. Perhaps a picture of palm trees and a beach? I will leave it to you for interpretation.

Across the screen I would like the words "Does your business have an exit plan?"

Below that it should read the following:
Let us help you with a completely impartial, no obligation assessment (button with link to the contact page)

Also, please use logo in a prominent place on the website so it's easily seen.

Target Market(s)

Males 40+

Coding

Coded - Design and coding required

Number of Pages Required

5+ page

Colors

Designer to choose colors to be used in the design.

Requirements
Must have
• The tabs for the homepage on the top should be:
• 1. About us
• 2. Services
• 3. Industries
• 4. Our success
• 5. Contact
Nice to have
• Clean, professional image.
• Please put FB, Twitter, Linked In - logos at bottom.
• Here are two examples of a website to give you an idea:
• https://notes.quelvarocapital.example/library/why-every-business-owner-should-have-an-exit-plan
Should not have
• nothing whimsical or cartoon like

```html
<!DOCTYPE html>
<html lang="en">
<head>
<meta charset="utf-8">
<title>Marwick Partners — Exit Planning Advisors</title>
<link href="https://fonts.googleapis.com/css2?family=Playfair+Display:wght@400;700&family=Montserrat:wght@400;500;600;700&display=swap" rel="stylesheet">
<style>
:root{
  --navy:#0d2238;
  --blue:#1e90d6;
  --sky:#3fa7e6;
  --ink:#2b2b2b;
  --muted:#9a9a9a;
  --light:#f4f5f7;
  --white:#ffffff;
  --dark:#1f1f1f;
  --darker:#151515;
}
*{box-sizing:border-box;margin:0;padding:0}
html,body{width:1200px;height:3596px;overflow:hidden}
body{font-family:"Montserrat",sans-serif;color:var(--ink);background:var(--white);position:relative}
.serif{font-family:"Playfair Display",serif}
.abs{position:absolute}

/* hero */
.hero{position:absolute;left:0;top:0;width:1200px;height:790px;
  background:linear-gradient(180deg,#0a1c33 0%,#14406e 40%,#2e6fa8 70%,#7fa8cc 100%);overflow:hidden}
.hero-photo{position:absolute;inset:0;background:
  radial-gradient(ellipse at 72% 55%,rgba(200,225,245,.55),rgba(0,0,0,0) 45%),
  linear-gradient(90deg,rgba(10,25,50,.6),rgba(10,25,50,0) 60%)}
.brand{position:absolute;left:108px;top:26px;display:flex;align-items:center;gap:14px;color:var(--white)}
.brand-mark{width:40px;height:40px;background:var(--white)}
.brand-name{font-family:"Montserrat",sans-serif;font-size:22px;font-weight:500;letter-spacing:1px}
.nav{position:absolute;right:108px;top:96px;display:flex;gap:30px}
.nav a{color:var(--white);text-decoration:none;font-size:15px;font-weight:600;letter-spacing:.5px}
.nav a.active{border-bottom:2px solid var(--white);padding-bottom:4px}
.call{position:absolute;right:108px;top:150px;display:flex;align-items:center;gap:10px;color:var(--white);font-size:15px;font-weight:600}
.call b{font-size:19px}
.call-icon{width:32px;height:32px;border-radius:50%;background:var(--white);display:flex;align-items:center;justify-content:center}
.hero-box{position:absolute;left:96px;top:224px;width:690px;height:380px;background:rgba(255,255,255,.12);border:1px solid rgba(255,255,255,.25);padding:36px 30px}
.hero-box h1{font-family:"Playfair Display",serif;font-weight:400;color:var(--white);font-size:54px;line-height:66px;text-transform:uppercase}
.hero-box p{color:var(--white);font-size:16px;margin-top:34px}
.btn{display:inline-flex;align-items:center;gap:8px;font-size:13px;font-weight:700;letter-spacing:.5px;text-transform:uppercase;padding:14px 24px;text-decoration:none}
.btn-blue{background:var(--blue);color:var(--white);margin-top:26px}
.btn-dark{background:var(--darker);color:var(--white)}
.dots{position:absolute;right:40px;top:660px;display:flex;flex-direction:column;gap:10px}
.dots i{width:8px;height:8px;border-radius:50%;background:rgba(255,255,255,.5)}
.dots i:first-child{background:var(--white)}
.notch{position:absolute;left:0;top:740px}

/* welcome */
.welcome-img{position:absolute;left:140px;top:890px;width:360px;height:420px;background:linear-gradient(135deg,#6e6a64,#c9c4bc 50%,#4b4a47);border:14px solid #f1f1f1;outline:1px solid #ddd}
.welcome-text{position:absolute;left:560px;top:905px;width:500px}
.welcome-text h3{font-family:"Playfair Display",serif;font-weight:400;font-size:30px;letter-spacing:1px}
.welcome-text h2{font-family:"Playfair Display",serif;font-weight:400;font-size:40px;letter-spacing:1px;margin-top:6px}
.body-copy{font-size:14px;line-height:26px;color:var(--muted)}
.welcome-text .body-copy{margin-top:22px}
.welcome-text .btn{margin-top:34px}

/* what we do */
.services{position:absolute;left:0;top:1420px;width:1200px;height:520px;background:linear-gradient(180deg,var(--white),var(--light) 60%,var(--white))}
.services h2{position:absolute;left:160px;top:120px;font-family:"Playfair Display",serif;font-weight:400;font-size:40px}
.services .body-copy{position:absolute;left:510px;top:110px;width:560px}
.service-list{position:absolute;left:130px;top:280px;width:940px;display:flex;justify-content:space-between}
.service{width:200px;text-align:center;font-size:15px;font-weight:600}
.service svg{display:block;margin:0 auto 14px}
.services .btn{position:absolute;left:525px;top:432px}

.city{position:absolute;left:0;top:1940px;width:1200px;height:600px;
  background:linear-gradient(180deg,#ffffff 0%,#dfe7ef 25%,#9fb3c9 55%,#6b7f98 80%,#ffffff 100%)}

/* testimonials */
.clients{position:absolute;left:0;top:2640px;width:1200px;text-align:center}
.clients h2{font-family:"Playfair Display",serif;font-weight:400;font-size:40px}
.clients .body-copy{width:860px;margin:28px auto 0}
.cards{position:absolute;left:140px;top:232px;width:920px;display:flex;justify-content:space-between}
.card{width:290px}
.card-box{background:var(--white);box-shadow:0 4px 24px rgba(0,0,0,.12);height:190px;padding:22px 24px;text-align:center}
.quote{font-family:"Playfair Display",serif;font-size:44px;line-height:40px;font-weight:700;color:var(--ink)}
.card-box p{font-size:12px;line-height:22px;color:var(--muted);margin-top:8px}
.author{display:flex;align-items:center;gap:14px;margin:26px 0 0 76px;text-align:left}
.avatar{width:44px;height:44px;border-radius:50%;background:#b79a84}
.author b{display:block;font-size:15px;font-weight:500}
.author span{font-size:11px;color:var(--muted)}
.clients .btn{position:absolute;left:483px;top:572px}

/* footer */
.footer{position:absolute;left:0;top:3280px;width:1200px;height:316px;background:linear-gradient(180deg,var(--dark),#2d2d2d);text-align:center;color:var(--white)}
.social{display:flex;justify-content:center;gap:12px;margin-top:44px}
.social i{width:30px;height:30px;border:2px solid var(--white);border-radius:50%}
.fnav{display:flex;justify-content:center;gap:32px;margin-top:26px}
.fnav a{color:var(--white);font-size:15px;font-weight:600;text-decoration:none}
.copy{font-size:12px;margin-top:22px;color:#cfcfcf}
</style>
</head>
<body>

<section class="hero">
  <div class="hero-photo" role="img" aria-label="Two businessmen shaking hands in a glass office overlooking a city skyline"></div>
  <div class="brand"><span class="brand-mark"></span><span class="brand-name">MARWICK PARTNERS</span></div>
  <nav class="nav">
    <a href="#" class="active">HOME</a><a href="#">ABOUT US</a><a href="#">SERVICES</a><a href="#">INDUSTRIES</a><a href="#">OUR SUCCESS</a><a href="#">CONTACT</a>
  </nav>
  <div class="call">
    <span class="call-icon"><svg width="16" height="16" viewBox="0 0 24 24"><path d="M6.6 10.8a15 15 0 0 0 6.6 6.6l2.2-2.2a1 1 0 0 1 1-.25 11 11 0 0 0 3.6.6 1 1 0 0 1 1 1V20a1 1 0 0 1-1 1A17 17 0 0 1 3 4a1 1 0 0 1 1-1h3.5a1 1 0 0 1 1 1 11 11 0 0 0 .6 3.6 1 1 0 0 1-.25 1z" fill="#0d2238"/></svg></span>
    CALL US : <b>1 800 555 0142</b>
  </div>
  <div class="hero-box">
    <h1>Does your business<br>have an exit plan?</h1>
    <p>Let us help you with a completely impartial, no obligation assessment</p>
    <a class="btn btn-blue" href="#">Contact us <span>&#10140;</span></a>
  </div>
  <div class="dots"><i></i><i></i><i></i></div>
  <svg class="notch" width="1200" height="52" viewBox="0 0 1200 52"><path d="M0 52V50h560l40-34 40 34h560v2z" fill="#fff"/></svg>
</section>

<section>
  <div class="welcome-img" role="img" aria-label="Overhead view of a team meeting around a table with documents"></div>
  <div class="welcome-text">
    <h3>WELCOME TO</h3>
    <h2>MARWICK PARTNERS</h2>
    <p class="body-copy">Lorem ipsum dolor sit amet, consectetur adipiscing elit, sed do eiusmod tempor incididunt ut labore et dolore magna aliqua. Ut enim ad minim veniam, quis nostrud exercitation ullamco laboris nisi ut aliquip ex ea commodo consequat. Duis aute irure dolor in reprehenderit in voluptate velit esse cillum dolore eu fugiat nulla pariatur sint occaecat.</p>
    <a class="btn btn-dark" href="#">Read more <span>&#10140;</span></a>
  </div>
</section>

<section class="services">
  <h2>WHAT WE DO</h2>
  <p class="body-copy">Lorem ipsum dolor sit amet, consectetur adipiscing elit, sed do eiusmod tempor incididunt ut labore et dolore magna aliqua. Ut enim ad minim veniam, quis nostrud exercitation ullamco laboris nisi ut aliquip.</p>
  <div class="service-list">
    <div class="service"><svg width="48" height="40" viewBox="0 0 48 40" fill="none" stroke="#222" stroke-width="2"><path d="M4 14l10-6 10 6 10-6 10 6M14 8v20M34 8v20M8 30h32"/></svg>Lorem ipsum</div>
    <div class="service"><svg width="48" height="40" viewBox="0 0 48 40" fill="none" stroke="#222" stroke-width="2"><path d="M6 36h36M10 36V26M20 36V20M30 36V14M40 36V8M8 22l12-10 8 6 14-12"/></svg>Accusantium viore</div>
    <div class="service"><svg width="48" height="40" viewBox="0 0 48 40" fill="none" stroke="#222" stroke-width="2"><circle cx="24" cy="20" r="16"/><path d="M16 20l6 6 12-12"/></svg>Nemo enim ipsa</div>
    <div class="service"><svg width="48" height="40" viewBox="0 0 48 40" fill="none" stroke="#222" stroke-width="2"><rect x="10" y="4" width="28" height="32"/><path d="M16 13h16M16 20h16M16 27h10"/></svg>Tempora incidun</div>
  </div>
  <a class="btn btn-dark" href="#">View more <span>&#10140;</span></a>
</section>

<div class="city" role="img" aria-label="Businessman seen from behind looking over a city skyline at sunrise"></div>

<section class="clients">
  <h2>WHAT CLIENTS SAY</h2>
  <p class="body-copy">Lorem ipsum dolor sit amet, consectetur adipiscing elit, sed do eiusmod tempor incididunt ut labore et dolore magna aliqua. Ut enim ad minim veniam, quis nostrud exercitation ullamco laboris nisi ut aliquip ex ea commodo.</p>
  <div class="cards">
    <div class="card">
      <div class="card-box"><div class="quote">&ldquo;</div><p>Lorem ipsum dolor sit amet consectetur adipiscing elit sed do eiusmod tempor incididunt ut labore et dolore magna aliqua enim minim veniam.</p></div>
      <div class="author"><span class="avatar"></span><div><b>By Client Name</b><span>City, Location</span></div></div>
    </div>
    <div class="card">
      <div class="card-box"><div class="quote">&ldquo;</div><p>Lorem ipsum dolor sit amet consectetur adipiscing elit sed do eiusmod tempor incididunt ut labore et dolore magna aliqua enim minim veniam.</p></div>
      <div class="author"><span class="avatar" style="background:#8e7563"></span><div><b>By Client Name</b><span>City, Location</span></div></div>
    </div>
    <div class="card">
      <div class="card-box"><div class="quote">&ldquo;</div><p>Lorem ipsum dolor sit amet consectetur adipiscing elit sed do eiusmod tempor incididunt ut labore et dolore magna aliqua enim minim veniam.</p></div>
      <div class="author"><span class="avatar" style="background:#a88a70"></span><div><b>By Client Name</b><span>City, Location</span></div></div>
    </div>
  </div>
  <a class="btn btn-dark" href="#">View more reviews <span>&#10140;</span></a>
</section>

<footer class="footer">
  <div class="social"><i></i><i></i><i></i></div>
  <nav class="fnav"><a href="#">HOME</a><a href="#">ABOUT US</a><a href="#">SERVICES</a><a href="#">INDUSTRIES</a><a href="#">OUR SUCCESS</a><a href="#">CONTACT</a></nav>
  <p class="copy">© 2020 Marwick Partners All right reserved. Terms of Use | Privacy policy</p>
</footer>

</body>
</html>
```